Thornvale Group needs a business card design

We need a new business card design using the logo recently selected in a logo competition on Pixel Bazaar. Our business is a consultancy specializing in aviation and energy and the winning business card design will promote an image of precision and professionalism with creativity.

Please use the logo with the name on the front of the card and use a complementary font. Make the back white with either the light grey or dark grey logo.

Target Market(s)

Senior finance and legal leaders at aviation and energy companies

Industry/Entity Type

Management Consulting

Contact Information for Business Card

Peter Castrell
President
Thornvale Group

www.thornvalegroup.example

(555) 204-6391
pc@thornvalegroup.example

Requirements
Must have
• Professional font that goes well with the logo font

```html
<!DOCTYPE html>
<html lang="en">
<head>
<meta charset="utf-8">
<title>Thornvale Group — Business Card</title>
<link href="https://fonts.googleapis.com/css2?family=Open+Sans:wght@300;400;700&display=swap" rel="stylesheet">
<style>
  :root {
    --backdrop: #e9e7e3;
    --card-dark: #262626;
    --card-light: #ffffff;
    --navy: #16406f;
    --slate: #616365;
    --text-grey: #5a5a5a;
    --white: #ffffff;
  }
  html, body {
    margin: 0;
    padding: 0;
    width: 1200px;
    height: 900px;
    overflow: hidden;
    background: var(--backdrop);
    font-family: "Open Sans", Arial, sans-serif;
  }
  .canvas {
    position: relative;
    width: 1200px;
    height: 900px;
  }
  .card {
    position: absolute;
    left: 280px;
    width: 640px;
    height: 366px;
    box-shadow: 0 6px 18px rgba(0,0,0,0.18);
    overflow: hidden;
  }

  /* Reverse side */
  .card--reverse {
    top: 60px;
    background: var(--card-dark);
    color: var(--white);
  }
  .reverse-wordmark {
    position: absolute;
    left: 0;
    right: 0;
    top: 118px;
    text-align: center;
    font-size: 44px;
    font-weight: 400;
    letter-spacing: 2px;
    color: var(--white);
  }
  .reverse-tagline {
    position: absolute;
    left: 190px;
    top: 218px;
  }
  .reverse-tagline__title {
    margin: 0;
    font-size: 17px;
    font-weight: 700;
  }
  .reverse-tagline__sectors {
    margin: 2px 0 0;
    font-size: 16px;
    font-weight: 300;
  }

  /* Front side */
  .card--front {
    top: 474px;
    background: var(--card-light);
  }
  .card-graphics {
    position: absolute;
    inset: 0;
  }
  .identity {
    position: absolute;
    left: 66px;
    top: 22px;
  }
  .identity__name {
    margin: 0;
    font-size: 20px;
    font-weight: 700;
    color: var(--navy);
    line-height: 1.1;
  }
  .identity__role {
    margin: 0;
    font-size: 13px;
    color: var(--text-grey);
  }
  .contact {
    position: absolute;
    left: 28px;
    top: 176px;
    margin: 0;
    padding: 0;
    list-style: none;
    font-size: 15px;
    color: var(--text-grey);
  }
  .contact__item {
    display: flex;
    align-items: center;
    gap: 8px;
    margin-bottom: 4px;
  }
  .contact__icon {
    width: 12px;
    height: 12px;
    fill: var(--navy);
    flex: none;
  }
  .front-wordmark {
    position: absolute;
    right: 40px;
    top: 196px;
    display: flex;
    align-items: center;
    gap: 10px;
    font-size: 30px;
    font-weight: 400;
    letter-spacing: 1px;
    color: var(--navy);
  }
  .front-wordmark__square {
    width: 14px;
    height: 14px;
    background: var(--navy);
  }
</style>
</head>
<body>
<main class="canvas">

  <section class="card card--reverse" aria-label="Card reverse">
    <div class="reverse-wordmark">Thornvale Group</div>
    <div class="reverse-tagline">
      <p class="reverse-tagline__title">Finance and Strategy Consulting</p>
      <p class="reverse-tagline__sectors">Aviation - Manufacturing - Energy</p>
    </div>
  </section>

  <section class="card card--front" aria-label="Card front">
    <svg class="card-graphics" width="640" height="366" viewBox="0 0 640 366" aria-hidden="true">
      <polygon class="corner-mark-grey" points="0,0 44,0 44,36 0,36" fill="var(--slate)"/>
      <polygon class="corner-mark-navy" points="22,36 50,4 58,4 58,36" fill="var(--navy)"/>
      <polygon class="band-grey" points="0,258 300,258 286,296 0,296" fill="var(--slate)"/>
      <polygon class="band-navy" points="298,296 640,296 640,344 282,344" fill="var(--navy)"/>
    </svg>

    <div class="identity">
      <p class="identity__name">Peter Castrell</p>
      <p class="identity__role">President</p>
    </div>

    <ul class="contact">
      <li class="contact__item">
        <svg class="contact__icon" viewBox="0 0 24 24" aria-hidden="true"><path d="M6.6 10.8a15.1 15.1 0 0 0 6.6 6.6l2.2-2.2a1 1 0 0 1 1-.25 11.4 11.4 0 0 0 3.6.57 1 1 0 0 1 1 1V20a1 1 0 0 1-1 1A17 17 0 0 1 3 4a1 1 0 0 1 1-1h3.5a1 1 0 0 1 1 1c0 1.25.2 2.45.57 3.57a1 1 0 0 1-.25 1z"/></svg>
        <span>(555) 204-6391</span>
      </li>
      <li class="contact__item">
        <svg class="contact__icon" viewBox="0 0 24 24" aria-hidden="true"><path d="M2 5h20v14H2z M3 6l9 7 9-7" fill="var(--navy)" stroke="#fff" stroke-width="1.5"/></svg>
        <span>pc@thornvalegroup.example</span>
      </li>
    </ul>

    <div class="front-wordmark">
      <span class="front-wordmark__square"></span>
      <span>Thornvale Group</span>
    </div>
  </section>

</main>
</body>
</html>
```